Business Card Design

We are a manufacturing and distribution company with most of our customer base being supermarkets. We have established brand guidelines that are attached.

```html
<!DOCTYPE html>
<html lang="en">
<head>
<meta charset="utf-8">
<title>Valmora Business Card</title>
<link href="https://fonts.googleapis.com/css2?family=Montserrat:wght@400;500;600;800&display=swap" rel="stylesheet">
<style>
  :root {
    --backdrop: #7b7b7b;
    --paper: #ffffff;
    --brand-blue: #0a63b8;
    --brand-blue-dark: #0657a6;
    --brand-red: #e4141c;
    --ink: #111111;
    --ink-soft: #4a4a4a;
  }
  * { margin: 0; padding: 0; box-sizing: border-box; }
  html, body {
    width: 1200px;
    height: 1056px;
    overflow: hidden;
    background: var(--backdrop);
    font-family: "Montserrat", sans-serif;
  }
  .sheet {
    position: relative;
    width: 1200px;
    height: 1056px;
  }
  .card {
    position: absolute;
    left: 340px;
    width: 520px;
    height: 297px;
    border-radius: 3px;
    box-shadow: 0 14px 30px rgba(0,0,0,0.25);
  }
  .card-front {
    top: 170px;
    background: var(--paper);
  }
  .card-back {
    top: 590px;
    background: linear-gradient(135deg, #0b6cc4 0%, var(--brand-blue) 50%, var(--brand-blue-dark) 100%);
  }

  /* Front */
  .holder {
    position: absolute;
    left: 40px;
    top: 40px;
  }
  .holder-name {
    font-size: 21px;
    font-weight: 500;
    letter-spacing: 0.5px;
    line-height: 1;
    color: var(--brand-blue);
  }
  .holder-name .first {
    font-weight: 800;
    color: var(--brand-red);
  }
  .holder-role {
    margin-top: 4px;
    font-size: 12px;
    color: var(--ink-soft);
  }
  .contact-list {
    position: absolute;
    right: 40px;
    top: 112px;
    list-style: none;
  }
  .contact-item {
    display: flex;
    align-items: center;
    justify-content: flex-end;
    gap: 8px;
    font-size: 11px;
    color: var(--ink-soft);
    margin-bottom: 6px;
  }
  .contact-icon {
    width: 16px;
    height: 16px;
    border-radius: 3px;
    background: var(--brand-blue);
    display: flex;
    align-items: center;
    justify-content: center;
  }
  .brand-front {
    position: absolute;
    right: 40px;
    bottom: 36px;
    display: flex;
    align-items: center;
    gap: 10px;
    font-size: 28px;
    font-weight: 800;
    letter-spacing: 1px;
    color: var(--ink);
  }
  .brand-square {
    width: 18px;
    height: 18px;
    background: var(--brand-blue);
  }

  /* Back */
  .brand-back {
    position: absolute;
    left: 70px;
    top: 110px;
    font-size: 40px;
    font-weight: 800;
    letter-spacing: 2px;
    color: var(--paper);
  }
</style>
</head>
<body>
<main class="sheet">
  <section class="card card-front">
    <div class="holder">
      <p class="holder-name"><span class="first">DANA</span> KESSLER</p>
      <p class="holder-role">Manager</p>
    </div>
    <ul class="contact-list">
      <li class="contact-item">(555) 014-2870
        <span class="contact-icon">
          <svg width="10" height="10" viewBox="0 0 10 10"><path d="M2 1 L3.6 1 L4.2 3 L3.2 3.8 Q4 5.8 6.2 6.8 L7 5.8 L9 6.4 L9 8 Q8.6 9 7.6 9 Q1 8.4 1 2 Q1 1 2 1 Z" fill="#fff"/></svg>
        </span>
      </li>
      <li class="contact-item">info@valmoramail.com
        <span class="contact-icon">
          <svg width="11" height="9" viewBox="0 0 11 9"><rect x="0.6" y="0.6" width="9.8" height="7.8" fill="none" stroke="#fff" stroke-width="1.2"/><path d="M0.6 0.6 L5.5 5 L10.4 0.6" fill="none" stroke="#fff" stroke-width="1.2"/></svg>
        </span>
      </li>
      <li class="contact-item">www.valmora.com
        <span class="contact-icon">
          <svg width="10" height="10" viewBox="0 0 10 10"><path d="M2 1 L8 5.5 L5.4 5.8 L6.8 8.8 L5.6 9.3 L4.3 6.3 L2.4 8 Z" fill="#fff"/></svg>
        </span>
      </li>
    </ul>
    <div class="brand-front">
      <span class="brand-square"></span>
      <span class="brand-name">VALMORA</span>
    </div>
  </section>

  <section class="card card-back">
    <p class="brand-back">VALMORA</p>
  </section>
</main>
</body>
</html>
```